Business Card Design

I'm a commercial general contractor remodel offices, hotels, health clubs and stores mostly San Francisco and the peninsula
the file I down loaded is kind of what I want I like the I beam with my company name in it, that would be fine with me but if you have better Idea will look at it you never know, I'm decided to give in and change my company name to how every one knows me, I have been in business since 1991, I like the I beam logo I included one of my old card from my old company for reference for you.

BROCK CONSTRUCTION (is my company name)
Warren Pelkey contractor, LIc 514387
3148 Larkspur Row, San Bruno, California 94071
mobile, (415) 736-4052
phone (650) 514-2087
Fax, (650) 514-2088
email, brock@brockconstruction.example

```html
<!DOCTYPE html>
<html lang="en">
<head>
<meta charset="utf-8">
<title>Brock Construction – Business Card</title>
<link href="https://fonts.googleapis.com/css2?family=Cinzel:wght@700&family=Open+Sans:wght@400;600;700&display=swap" rel="stylesheet">
<style>
  :root {
    --backdrop: #e9e9e7;
    --card: #fbfbfa;
    --blue: #1e8ccb;
    --navy: #25358a;
    --ink: #1f2d78;
  }
  * { margin: 0; padding: 0; box-sizing: border-box; }
  html, body { width: 1200px; height: 800px; overflow: hidden; }
  body { background: var(--backdrop); font-family: "Open Sans", Arial, sans-serif; }

  .card {
    position: absolute; left: 75px; top: 100px;
    width: 1050px; height: 600px;
    background: var(--card);
    box-shadow: 0 8px 24px rgba(0,0,0,.18);
    overflow: hidden;
  }
  .card-shapes { position: absolute; inset: 0; }
  .shape-blue { fill: var(--blue); }
  .shape-card { fill: var(--card); }

  .brand { position: absolute; left: 48px; top: 70px; }
  .brand-mark {
    display: flex; align-items: center; gap: 14px;
    font-weight: 700; font-size: 64px; color: var(--navy); line-height: 1;
  }
  .brand-square { width: 34px; height: 34px; background: var(--navy); }
  .brand-name {
    margin-top: 10px;
    font-weight: 700; font-size: 40px; color: var(--blue); letter-spacing: .5px;
  }

  .address {
    position: absolute; left: 48px; bottom: 40px;
    font-size: 17px; color: var(--ink); line-height: 1.4;
  }

  .contact { position: absolute; right: 40px; top: 188px; text-align: right; color: var(--ink); }
  .person-name { font-family: "Cinzel", Georgia, serif; font-size: 40px; letter-spacing: 1px; line-height: 1.1; }
  .person-role { font-size: 26px; color: var(--ink); margin-top: -2px; }
  .lines { margin-top: 26px; list-style: none; }
  .lines li { font-size: 32px; line-height: 54px; display: flex; justify-content: flex-end; align-items: center; gap: 16px; }
  .icon { width: 26px; height: 26px; fill: var(--blue); }

  .email {
    position: absolute; right: 40px; bottom: 36px;
    font-size: 25px; color: var(--ink); white-space: nowrap;
    display: flex; align-items: center; gap: 12px;
  }
  .email .icon { fill: none; stroke: var(--blue); stroke-width: 2; width: 28px; height: 20px; }
</style>
</head>
<body>
  <section class="card" aria-label="Brock Construction business card">
    <svg class="card-shapes" viewBox="0 0 1050 600" aria-hidden="true">
      <polygon class="shape-blue" points="300,215 560,215 440,600"/>
      <polygon class="shape-blue" points="640,0 1050,0 1050,170 650,170 640,205 1050,205 1050,600 490,600"/>
      <polygon class="shape-card" points="664,178 1050,178 1050,262 644,262"/>
      <polygon class="shape-card" points="615,290 1050,290 1050,562 528,562"/>
    </svg>

    <div class="brand">
      <div class="brand-mark"><span class="brand-square"></span>BRC, INC.</div>
      <div class="brand-name">BROCK CONSTRUCTION</div>
    </div>

    <div class="address">3148 Larkspur Row, San Bruno, CA 94071</div>

    <div class="contact">
      <div class="person-name">WARREN PELKEY</div>
      <div class="person-role">contractor, Lic 514387</div>
      <ul class="lines">
        <li>
          <svg class="icon" viewBox="0 0 24 24"><path d="M6.6 10.8a15 15 0 0 0 6.6 6.6l2.2-2.2c.3-.3.7-.4 1-.2 1.1.4 2.3.6 3.6.6.6 0 1 .4 1 1V20c0 .6-.4 1-1 1A17 17 0 0 1 3 4c0-.6.4-1 1-1h3.5c.6 0 1 .4 1 1 0 1.3.2 2.5.6 3.6.1.3 0 .7-.2 1z"/></svg>
          (415) 736-4052
        </li>
        <li>
          <svg class="icon" viewBox="0 0 24 24"><path d="M6.6 10.8a15 15 0 0 0 6.6 6.6l2.2-2.2c.3-.3.7-.4 1-.2 1.1.4 2.3.6 3.6.6.6 0 1 .4 1 1V20c0 .6-.4 1-1 1A17 17 0 0 1 3 4c0-.6.4-1 1-1h3.5c.6 0 1 .4 1 1 0 1.3.2 2.5.6 3.6.1.3 0 .7-.2 1z"/></svg>
          (650) 514-2087
        </li>
        <li>
          <svg class="icon" viewBox="0 0 24 24"><path d="M7 2h10v6H7zM4 9h16a2 2 0 0 1 2 2v6h-4v5H6v-5H2v-6a2 2 0 0 1 2-2zm4 8v3h8v-3z"/></svg>
          (650) 514-2088
        </li>
      </ul>
    </div>

    <div class="email">
      <svg class="icon" viewBox="0 0 30 22"><rect x="1" y="1" width="28" height="20"/><path d="M1 1l14 11L29 1"/></svg>
      brock@brockconstruction.example
    </div>
  </section>
</body>
</html>
```